American cannabis tech company business card design

Pavrel.com is seeking a modern, professional, and brand-aligned business card that represents our company and its core values: Mission, Story, Values, and Impact. As an innovative cannabis company, we want a business card that is not only visually appealing but also serves as a representation of who we are and what we stand for.

Project Scope: Design a double-sided business card that integrates our brand identity and core values. Incorporate our key brand elements, ensuring a sleek and contemporary aesthetic. Visually reflect our core values (Mission, Story, Values, Impact) in a way that is engaging yet professional.

Target Market(s)

Vendors, third parties,

Contact Information for Business Card

Contact details (name, title, email, phone, website, etc.)

Font styles to use
Other font styles liked:
• Caslon, Centra

Colors

Designer to choose colors to be used in the design.

Requirements
Must have
• Pavrel.com logo and branding A creative yet clean way to integrate our core values (Mission, Story, Values, Impact) Modern typography and a well-structured layout
Nice to have
• forest green, grey, white, black
Should not have
• references to marijuana, leafs, plants, or related product

```html
<!DOCTYPE html>
<html lang="en">
<head>
<meta charset="utf-8">
<title>Pavrel.com Business Card</title>
<link rel="stylesheet" href="https://fonts.googleapis.com/css2?family=Montserrat:wght@400;700;800&display=swap">
<style>
  :root {
    --backdrop: #d3d8d7;
    --paper: #efefec;
    --forest: #0f2a16;
    --forest-deep: #0b1f10;
    --ink-grey: #3f4440;
    --cream: #ecebe7;
  }
  * { margin: 0; padding: 0; box-sizing: border-box; }
  html, body {
    width: 1200px; height: 881px; overflow: hidden;
    background: var(--backdrop);
    font-family: "Montserrat", sans-serif;
  }
  .stage {
    position: relative; width: 1200px; height: 881px;
  }
  .card {
    position: absolute; top: 297px;
    width: 510px; height: 287px;
    border-radius: 3px;
    box-shadow: 0 14px 30px rgba(40, 50, 48, 0.18);
  }
  .card--front { left: 75px; background: var(--paper); }
  .card--back {
    left: 615px; background: var(--forest);
    display: flex; align-items: center; justify-content: center;
  }
  .identity {
    position: absolute; right: 270px; top: 106px;
    text-align: right;
  }
  .identity__name {
    font-weight: 800; font-size: 21px; letter-spacing: 0.5px;
    color: var(--forest);
  }
  .identity__title {
    margin-top: 4px;
    font-weight: 400; font-size: 14px; color: var(--ink-grey);
  }
  .divider {
    position: absolute; left: 255px; top: 100px;
    width: 1.5px; height: 76px; background: var(--forest);
  }
  .contacts {
    position: absolute; left: 274px; top: 98px;
    list-style: none;
  }
  .contacts__item {
    display: flex; align-items: center; gap: 9px;
    font-size: 14px; color: var(--ink-grey);
    height: 26px;
  }
  .contacts__icon { width: 12px; height: 12px; fill: var(--forest); flex: none; }
  .wordmark {
    font-weight: 800; font-size: 84px; letter-spacing: 2px;
    color: var(--cream);
  }
</style>
</head>
<body>
  <main class="stage">
    <section class="card card--front" aria-label="Card front">
      <div class="identity">
        <p class="identity__name">DANIEL REYES</p>
        <p class="identity__title">Managing Director</p>
      </div>
      <div class="divider"></div>
      <ul class="contacts">
        <li class="contacts__item">
          <svg class="contacts__icon" viewBox="0 0 24 24" aria-hidden="true"><path d="M6.6 10.8a15.5 15.5 0 0 0 6.6 6.6l2.2-2.2a1 1 0 0 1 1-.25 11.4 11.4 0 0 0 3.6.57 1 1 0 0 1 1 1V20a1 1 0 0 1-1 1A17 17 0 0 1 3 4a1 1 0 0 1 1-1h3.5a1 1 0 0 1 1 1c0 1.25.2 2.45.57 3.57a1 1 0 0 1-.25 1z"/></svg>
          +1 405-555-0143
        </li>
        <li class="contacts__item">
          <svg class="contacts__icon" viewBox="0 0 24 24" aria-hidden="true"><path d="M2 5h20v14H2z M2 5l10 8 10-8" fill="var(--forest)"/><path d="M2 6l10 7 10-7" fill="none" stroke="var(--paper)" stroke-width="1.6"/></svg>
          team@pavrel.com
        </li>
        <li class="contacts__item">
          <svg class="contacts__icon" viewBox="0 0 24 24" aria-hidden="true"><circle cx="12" cy="12" r="10"/><path d="M2 12h20M12 2c3 3 3 17 0 20M12 2c-3 3-3 17 0 20" fill="none" stroke="var(--paper)" stroke-width="1.5"/></svg>
          www.pavrel.com
        </li>
      </ul>
    </section>

    <section class="card card--back" aria-label="Card back">
      <p class="wordmark">PAVREL</p>
    </section>
  </main>
</body>
</html>
```